Norvane Website Design (New Start Up Investment Management Firm)

We need a website designed. We have attached a Powerpoint with our proposed website content (which is quite minimal), the format is just a suggestion but we would like to see your alternative and improved ideas. We are a boutique investment firm so are looking for something sleek and professional. I have included on the last page of the attachment our brand colours and font styles as well as attaching our logo design. We would like the successful designer to design the website and build the buttons etc.

On the "Contact Us" page, we are open to suggestions on how best to show the map, whether is should be static or open a google maps page. We would like the phone number and email address to be set up so people can click on them on their phone and it calls us or emails us directly.

We would prefer not to have photos of landscapes on the site.
Our website is hosted on a Linux based website.

We would also like 3 links at the bottom of each page for links to pdfs:
- Disclaimer, Terms and Conditions of Web Site Use
- Stewardship
- Pillar III

Target Market(s)

Institutional Investors

Industry/Entity Type

Investment

Coding

Coded - Design and coding required

Number of Pages Required

3 page

Font styles to use
Other font styles liked:
• Logo: Lato, Text: Source Sans Pro

Colors

Designer to choose colors to be used in the design.

Requirements
Must have
• The website must use the colours and fonts on the last page of the attached powerpoint. I can't see an option to select the exact colour palette below so please look at the PPT.
• For others please see Project description.
Should not have
• Landscape photos

```html
<!DOCTYPE html>
<html lang="en">
<head>
<meta charset="utf-8">
<title>Norvane Investment Management</title>
<link rel="stylesheet" href="https://fonts.googleapis.com/css2?family=Lato:wght@400;700;900&family=Source+Sans+3:wght@400;600&display=swap">
<style>
:root{
  --navy:#0b2c5c;
  --sky:#5aa8de;
  --band:#6ab1e4;
  --grey-bg:#f5f5f5;
  --text:#6b6b6b;
  --white:#ffffff;
}
*{margin:0;padding:0;box-sizing:border-box}
html,body{width:694px;height:1200px;overflow:hidden;background:#fff}
body{font-family:"Source Sans 3",sans-serif;color:var(--text);position:relative}
.page{position:relative;width:694px;height:1200px}

.hero{position:absolute;left:0;top:0;width:694px;height:373px;
  background:linear-gradient(180deg,#b49670 0%,#c9a77c 35%,#8d6b4f 70%,#4f4036 100%)}
.hero-glow{position:absolute;inset:0;background:radial-gradient(ellipse at 55% 45%,rgba(255,226,170,.55),rgba(255,226,170,0) 60%)}
.brand{position:absolute;left:0;right:0;text-align:center;color:var(--white);font-family:"Lato",sans-serif}
.brand-row{display:inline-flex;align-items:center;gap:10px}
.brand-mark{width:30px;height:30px;background:var(--white)}
.brand-name{font-weight:400;font-size:36px;letter-spacing:1px;line-height:1}
.brand-sub{font-size:7px;letter-spacing:2.5px;margin-top:3px;margin-left:42px;text-align:left}
.hero .brand{top:66px}
.nav{position:absolute;top:143px;left:99px;display:flex;gap:0;font-family:"Lato",sans-serif;font-weight:700;font-size:11px;color:var(--white)}
.nav a{color:inherit;text-decoration:none;margin-right:35px}
.hero-title{position:absolute;top:226px;left:0;right:0;text-align:center;font-family:"Lato",sans-serif;font-weight:700;font-size:18px;color:var(--white);letter-spacing:.2px}
.hero-cta{position:absolute;top:272px;left:262px;width:171px;height:28px;border:1.5px solid var(--white);color:var(--white);font-family:"Lato",sans-serif;font-weight:700;font-size:13px;display:flex;align-items:center;justify-content:center}

.section-title{position:absolute;left:0;right:0;text-align:center;font-family:"Lato",sans-serif;font-weight:900;font-size:23px;color:var(--navy)}
.section-title span{color:var(--sky)}
.copy{position:absolute;text-align:center;font-size:6.6px;line-height:12px;color:var(--text)}

.about-title{top:394px}
.about-copy{top:431px;left:78px;width:540px}
.about-media{position:absolute;top:480px;left:128px;width:438px;height:174px;background:linear-gradient(120deg,#8a6b55 0%,#c8b9a8 45%,#9a8776 75%,#5b4a40 100%)}
.play{position:absolute;left:211px;top:79px}
.philosophy{top:674px;left:78px;width:540px}
.philosophy b{font-family:"Lato",sans-serif;font-size:8.5px;color:var(--navy)}

.approach{position:absolute;top:732px;left:0;width:694px;height:283px;background:var(--grey-bg)}
.approach-title{top:752px}
.approach-copy{top:788px;left:72px;width:550px}
.card{position:absolute;top:846px;width:157px}
.card-media{height:120px}
.card-label{margin-top:10px;font-family:"Lato",sans-serif;font-size:14px;letter-spacing:.6px;color:var(--navy)}
.card-1{left:77px}.card-1 .card-media{background:linear-gradient(135deg,#e9e3da,#b39a7a 60%,#d9d2c7)}
.card-2{left:269px}.card-2 .card-media{background:linear-gradient(135deg,#d9b7c4,#5a7fb8 55%,#1f3d78)}
.card-3{left:459px}.card-3 .card-media{background:linear-gradient(135deg,#d9b39a,#3b4d63 55%,#1e2836)}
.card-2 .card-label{margin-top:12px}

.subscribe{position:absolute;top:1015px;left:0;width:694px;height:80px;background:var(--band);color:var(--white)}
.subscribe h2{position:absolute;top:19px;left:54px;font-family:"Lato",sans-serif;font-weight:700;font-size:16px}
.subscribe p{position:absolute;top:46px;left:54px;font-family:"Lato",sans-serif;font-size:11.5px}
.subscribe-field{position:absolute;top:26px;left:391px;width:248px;height:28px;border:1.5px solid var(--white);display:flex;align-items:center;justify-content:space-between;padding:0 7px 0 8px;font-size:9px}

.footer{position:absolute;top:1095px;left:0;width:694px;height:105px;background:var(--navy);color:var(--white)}
.footer .brand{top:17px}
.footer .brand-mark{width:24px;height:24px}
.footer .brand-name{font-size:29px}
.footer .brand-sub{font-size:5.5px;margin-left:34px}
.footer-links{position:absolute;top:63px;left:0;right:0;display:flex;justify-content:center;gap:24px;font-family:"Lato",sans-serif;font-size:7px}
.footer-copy{position:absolute;top:86px;left:0;right:0;text-align:center;font-family:"Lato",sans-serif;font-size:6px}
</style>
</head>
<body>
<div class="page">

  <header class="hero">
    <div class="hero-glow" role="img" aria-label="Warm sunlit city street with a clock tower and red double-decker bus"></div>
    <div class="brand">
      <div class="brand-row"><div class="brand-mark"></div><div class="brand-name">NORVANE</div></div>
      <div class="brand-sub">INVESTMENT MANAGEMENT</div>
    </div>
    <nav class="nav">
      <a>About Us</a><a>Services</a><a>Insights</a><a>Careers</a><a>Investors</a><a>Newsroom</a><a>Contact</a>
    </nav>
    <h1 class="hero-title">PROVIDING STRATEGIC ADVICE WHEN IT MATTERS MOST</h1>
    <div class="hero-cta">CONTACT US TODAY</div>
  </header>

  <h2 class="section-title about-title">ABOUT <span>NORVANE</span></h2>
  <p class="copy about-copy">Norvane Investment Management was founded in 2016 with a clear vision to create an independent and nimble firm focused on generating superior risk-adjusted returns. Norvane has designed an innovative investment approach which aims to harness the best elements of alternative investment management whilst reducing its recognised shortcomings. We are performance and client focused firm, committed to building lasting relationships, treating our clients like partners rather than revenue streams.</p>
  <div class="about-media" role="img" aria-label="Video still of a team meeting around a table in a bright office">
    <svg class="play" width="16" height="16" viewBox="0 0 16 16"><circle cx="8" cy="8" r="7" fill="none" stroke="#fff" stroke-width="1.6"/><path d="M6.3 4.8 L11 8 L6.3 11.2 Z" fill="#fff"/></svg>
  </div>
  <p class="copy philosophy"><b>Philosophy:</b> Norvane' philosophy is based on the understanding that financial markets tend to mean revert and that valuations and fundamentals matter. Norvane strives to construct a esilient portfolio diversified across asset classes, strategies and time horizons to achieve our target return objective. Freedom of idea expression enables us to react nimbly to market dislocations.</p>

  <section class="approach"></section>
  <h2 class="section-title approach-title">OUR <span>APPROACH</span></h2>
  <p class="copy approach-copy">Norvane combines asset allocation, macro trading, hedging and fund selection capabilities in an actively risk-managed portfolio. This model provides increased control, flexibility and liquidity while lowering the overall fee burden. Our risk posture and asset allocation are synchronised with our cycle and valuation frameworks. Bottom-up ideas are consistent with these top-down views. We look to protect against steep drawdowns in times of market stress, so that we are in a position to invest when risk premia and margins of safety are high.</p>

  <div class="card card-1"><div class="card-media" role="img" aria-label="Stacks of coins beside a pen on paperwork"></div><div class="card-label">Macro Trading</div></div>
  <div class="card card-2"><div class="card-media" role="img" aria-label="Blue financial chart overlay on a city skyline"></div><div class="card-label">Asset Allocation</div></div>
  <div class="card card-3"><div class="card-media" role="img" aria-label="Finger touching a screen showing a candlestick chart"></div><div class="card-label">Risk Managed</div></div>

  <section class="subscribe">
    <h2>Stay Connected With Us</h2>
    <p>Enter your email id to know more about us</p>
    <div class="subscribe-field">
      <span>enter your email</span>
      <svg width="15" height="13" viewBox="0 0 15 13"><path d="M1 5 H6 V2.5 L10.5 6.5 L6 10.5 V8 H1 Z" fill="#fff"/><path d="M9 1 H13.5 V12 H9" fill="none" stroke="#fff" stroke-width="1.6"/></svg>
    </div>
  </section>

  <footer class="footer">
    <div class="brand">
      <div class="brand-row"><div class="brand-mark"></div><div class="brand-name">NORVANE</div></div>
      <div class="brand-sub">INVESTMENT MANAGEMENT</div>
    </div>
    <div class="footer-links"><span>Disclaimer</span><span>Terms and Conditions</span><span>Stewardship</span><span>Pillar III</span></div>
    <div class="footer-copy">© 2017 Norvane Investment Management. All Rights Reserved.</div>
  </footer>

</div>
</body>
</html>
```